Lindqvar Foundation Letterhead

We are a newly established non profit registered in Maryland but operates in Africa, south of the sahara. We offer scholarships to deserving young adults from high school through college. Our color theme for our existing logo is purple, we want a design that is stylish, spellbinding yet a letterhead that projects seriousness. More information on www.thelindqvarfoundation.example

Target Market(s)

High school and college students in sub saharan African as well as our donors in the US

Industry/Entity Type

Non Profit

Font styles to use
Script

Requirements
Must have
• Logo at the top and if possible watermark the logo in the middle of the letterhead, contact address,
Should not have
• NA

```html
<!DOCTYPE html>
<html lang="en">
<head>
<meta charset="utf-8">
<title>Lindqvar Foundation Letterhead</title>
<link rel="stylesheet" href="https://fonts.googleapis.com/css2?family=Arimo:wght@400;700&family=Cormorant+Garamond:wght@500&family=Satisfy&display=swap">
<style>
  :root {
    --backdrop: #e9e9ea;
    --paper: #ffffff;
    --ink: #1c1c1c;
    --purple: #7b4fa6;
    --purple-soft: #b9a3d2;
    --watermark: #f3eff8;
  }
  * { box-sizing: border-box; margin: 0; padding: 0; }
  html, body { width: 1200px; height: 949px; overflow: hidden; }
  body {
    background: var(--backdrop);
    font-family: "Arimo", Arial, sans-serif;
    color: var(--ink);
    position: relative;
  }
  .letterhead {
    position: absolute;
    left: 289px; top: 34px;
    width: 622px; height: 880px;
    background: var(--paper);
    box-shadow: 0 2px 10px rgba(0,0,0,.12);
    overflow: hidden;
  }
  .watermark {
    position: absolute;
    right: -40px; top: 150px;
    width: 380px; height: 520px;
    border-radius: 50%;
    background: radial-gradient(ellipse at center, var(--watermark) 0%, rgba(243,239,248,.6) 45%, rgba(255,255,255,0) 72%);
  }
  .brand {
    position: absolute; left: 52px; top: 46px;
    display: flex; align-items: center; gap: 10px;
  }
  .brand-dot {
    width: 34px; height: 34px; border-radius: 50%;
    background: var(--purple);
  }
  .brand-name {
    font-size: 17px; color: var(--purple); font-weight: 400;
    letter-spacing: .5px;
  }
  .letter {
    position: absolute; left: 52px; top: 150px; width: 480px;
    display: flex; flex-direction: column;
  }
  .recipient {
    font-style: normal;
    font-size: 11px; line-height: 1.35;
    margin-bottom: 22px;
  }
  .recipient-name { font-weight: 700; font-size: 12px; }
  .body-copy {
    font-size: 11px; line-height: 1.55;
  }
  .body-copy p { margin-bottom: 16px; }
  .closing { font-size: 11px; margin-top: 8px; }
  .signature {
    margin: 6px 0 0 14px;
    font-family: "Satisfy", "Brush Script MT", cursive;
    font-size: 40px; line-height: 1.1; color: #111;
  }
  .signatory {
    margin: 4px 0 0 14px;
    font-size: 11px; font-weight: 700; line-height: 1.3;
  }
  .contact {
    position: absolute; left: 420px; top: 748px;
    border-left: 1.5px solid var(--purple);
    padding-left: 10px;
    font-size: 9.5px; line-height: 1.35;
  }
  .contact-label {
    font-family: "Cormorant Garamond", Georgia, serif;
    color: var(--purple); font-size: 11px; letter-spacing: 1px;
    font-weight: 500;
  }
  .contact-value { color: #333; margin-bottom: 6px; }
</style>
</head>
<body>
  <main class="letterhead">
    <div class="watermark" role="img" aria-label="Faint watermark area in soft lavender"></div>

    <header class="brand">
      <span class="brand-dot"></span>
      <span class="brand-name">Lindqvar Foundation Inc</span>
    </header>

    <article class="letter">
      <address class="recipient">
        <div class="recipient-name">JOHN SMITH</div>
        <div>Street Name,City Name.</div>
        <div>Zip Coad 0000</div>
      </address>

      <section class="body-copy">
        <p>Lorem Ipsum is simply dummy text of the printing and typesetting industry. Lorem Ipsum has been the industry's standard dummy text ever since the 1500s, when an unknown printer took a galley of type and scrambled it to make a type specimen book. It has survived not only five centuries, but also the leap into electronic typesetting, remaining essentially unchanged. It was popularised in the 1960s with the release of Typeleaf sheets containing Lorem Ipsum passages, and more recently with desktop publishing software like Folio PageSetter including versions of Lorem Ipsum.</p>
        <p>It is a long established fact that a reader will be distracted by the readable content of a page when looking at its layout. The point of using Lorem Ipsum is that it has a more-or-less normal distribution of letters, as opposed to using 'Content here, content here', making it look like readable English. Many desktop and web publishing packages and web page editors now use Lorem Ipsum as their default model text, and a search for 'lorem ipsum' will uncover many web sites still in their infancy. Various versions have evolved over the years, sometimes by accident, sometimes on purpose (injected humour and the like).</p>
      </section>

      <div class="closing">Regards,</div>
      <div class="signature">John Doe</div>
      <div class="signatory">John Doe<br>General Maneger</div>
    </article>

    <footer class="contact">
      <div class="contact-label">EMAIL:</div>
      <div class="contact-value">admin@thelindqvarfoundation.example</div>
      <div class="contact-label">WEB:</div>
      <div class="contact-value">www.thelindqvarfoundation.example</div>
    </footer>
  </main>
</body>
</html>
```